Black Car Limousine transportation business in Naples Florida

Always stand for my reliability and RVD stands for Love, K and M are the first initials of my children's names. It should show professionalism and a dedication to customer service. We keep our clients identities private. Show our professionalism. We are Black car Black tie company. We service transportation on a reserve basis to and from residents, airports, casinos, hotels,

Target Market(s)

It is a Private car service. High end clients. Businesses, Celebrity and athletes. Service to airports, hotels, special events.

Industry/Entity Type

Business

Contact Information for Business Card

A pearl metallic or Luster card. Standard business card size. Would like the name, Company email, show we take credit cards and phone number. Currently I don't have a website but will like to add later.

Logo Text

STEADFAST RVD TRANSPORTATION

Font styles to use
Serif

Colors
eaeaea
000000

Requirements
Must have
• Must have Company email, show we take credit cards and phone number. Currently I don't have a website but will like to add later.
Nice to have
• Would like to stay with a black and white theme. Open to some color trim.
Should not have
• Open to suggestions

```html
<!DOCTYPE html>
<html lang="en">
<head>
<meta charset="utf-8">
<title>Steadfast RVD Transportation – Business Card</title>
<link rel="stylesheet" href="https://fonts.googleapis.com/css2?family=Open+Sans:ital,wght@0,400;0,700;1,700&display=swap">
<style>
  :root {
    --stage: #3b3b3b;
    --card-light: #ffffff;
    --card-dark: #000000;
    --ink: #111111;
    --ink-soft: #444444;
    --brand-front: #8c8c8c;
    --brand-back: #b9b9b9;
    --silver-1: #7d7d7d;
    --silver-2: #f2f2f2;
    --silver-3: #9a9a9a;
  }
  html, body {
    margin: 0;
    padding: 0;
    width: 1105px;
    height: 1200px;
    overflow: hidden;
    background: var(--stage);
    font-family: "Open Sans", Arial, sans-serif;
  }
  .canvas { position: relative; width: 1105px; height: 1200px; }

  .card {
    position: absolute;
    left: 193px;
    width: 719px;
    height: 410px;
    overflow: hidden;
  }
  .card--front { top: 167px; background: var(--card-light); }
  .card--back  { top: 623px; background: var(--card-dark); }

  .vehicle-art {
    position: absolute;
    border-radius: 10px 14px 6px 6px;
  }
  .card--front .vehicle-art {
    left: 52px; top: 97px; width: 158px; height: 62px;
    background: linear-gradient(180deg, #3a3a3a 0%, #0c0c0c 60%, #222 100%);
  }
  .card--back .vehicle-art {
    left: 137px; top: 180px; width: 178px; height: 70px;
    background: linear-gradient(180deg, #5a5a5a 0%, #1a1a1a 55%, #333 100%);
  }

  .brand-name {
    position: absolute;
    margin: 0;
    font-weight: 700;
    line-height: 1;
    white-space: nowrap;
  }
  .card--front .brand-name {
    left: 226px; top: 118px;
    font-size: 20px;
    color: var(--brand-front);
  }
  .card--back .brand-name {
    left: 333px; top: 205px;
    font-size: 19px;
    color: var(--brand-back);
  }

  .holder { position: absolute; left: 52px; top: 276px; }
  .holder__name  { margin: 0; font-size: 24px; font-weight: 700; color: var(--ink); letter-spacing: .3px; }
  .holder__title { margin: 2px 0 0; font-size: 19px; color: var(--ink-soft); }

  .contact {
    position: absolute; left: 446px; top: 272px;
    list-style: none; margin: 0; padding: 0;
  }
  .contact__item {
    display: flex; align-items: center; gap: 10px;
    height: 28px; font-size: 19px; color: var(--ink-soft);
  }
  .contact__icon { width: 17px; height: 17px; fill: var(--ink); flex: none; }

  .trim { position: absolute; left: 0; bottom: 0; width: 100%; height: 15px; display: flex; }
  .trim__black  { width: 214px; background: #000; }
  .trim__gap    { width: 3px; background: #fff; }
  .trim__silver {
    flex: 1;
    background: linear-gradient(90deg, var(--silver-1) 0%, var(--silver-2) 35%, var(--silver-3) 60%, var(--silver-2) 85%, var(--silver-1) 100%);
  }

  .payment {
    position: absolute; left: 0; top: 333px; width: 100%; margin: 0;
    display: flex; justify-content: center; align-items: center; gap: 9px;
    color: #fff; font-size: 19px; font-weight: 700; font-style: italic;
  }
  .payment__icon { width: 28px; height: 20px; }
</style>
</head>
<body>
<div class="canvas">

  <section class="card card--front" aria-label="Business card front">
    <div class="vehicle-art" role="img" aria-label="Black luxury SUV illustration"></div>
    <p class="brand-name">STEADFAST RVD TRANSPORTATION</p>

    <div class="holder">
      <h1 class="holder__name">DANIEL REYES</h1>
      <p class="holder__title">CEO/Founder</p>
    </div>

    <ul class="contact">
      <li class="contact__item">
        <svg class="contact__icon" viewBox="0 0 24 24" aria-hidden="true"><path d="M6.6 10.8a15.1 15.1 0 0 0 6.6 6.6l2.2-2.2a1 1 0 0 1 1-.25 11.4 11.4 0 0 0 3.6.57 1 1 0 0 1 1 1V20a1 1 0 0 1-1 1A17 17 0 0 1 3 4a1 1 0 0 1 1-1h3.5a1 1 0 0 1 1 1c0 1.25.2 2.45.57 3.6a1 1 0 0 1-.25 1z"/></svg>
        239 555 0187
      </li>
      <li class="contact__item">
        <svg class="contact__icon" viewBox="0 0 24 24" aria-hidden="true"><path d="M2 6.2V19h20V6.2l-10 7.6z M2.8 5h18.4L12 12z"/></svg>
        ride@rvdtransport.com
      </li>
      <li class="contact__item">
        <svg class="contact__icon" viewBox="0 0 24 24" aria-hidden="true"><circle cx="12" cy="12" r="10"/><path d="M2 12h20M12 2c3 3 3 17 0 20M12 2c-3 3-3 17 0 20" fill="none" stroke="#fff" stroke-width="1.4"/></svg>
        www.rvdtransport.com
      </li>
    </ul>

    <div class="trim" aria-hidden="true">
      <span class="trim__black"></span><span class="trim__gap"></span><span class="trim__silver"></span>
    </div>
  </section>

  <section class="card card--back" aria-label="Business card back">
    <div class="vehicle-art" role="img" aria-label="Black luxury SUV illustration"></div>
    <p class="brand-name">STEADFAST RVD TRANSPORTATION</p>

    <p class="payment">
      <svg class="payment__icon" viewBox="0 0 28 20" aria-hidden="true">
        <rect x="1" y="2" width="26" height="16" rx="3" fill="#fff"/>
        <rect x="1" y="6" width="26" height="3" fill="#000"/>
        <rect x="4" y="12" width="8" height="2" fill="#000"/>
      </svg>
      We accept credit cards
    </p>
  </section>

</div>
</body>
</html>
```